We want to design total new business card and logo for Kestrel Building Services Ltd

Our company name Kestrel Building Services Ltd. Design new logo and business card , need hi-end luxury style art for architecture and construction industry. The card should simple but stylish. Our business focus on CONNECT tradesman to construction company, help marketing construction company tender oversea projects, managing franchise in construction sector, delivery amazing services to our client, so Logo should show the CONNECTION IDEA, CONNECTING PEOPLE, LUXURY. Visit our website for more information: kestrelgroup.example.nz

Target Market(s)

Directors or managers

Industry/Entity Type

Construction Company

Contact Information for Business Card

Name, Title, Mobile, Email, Website

Font styles to use
Serif

Colors

Designer to choose colors to be used in the design.

Requirements
Must have
• Simple and luxury, connection icon
Nice to have
• Special materials, plastic card, look through,...
• Look new ideas.

```html
<!DOCTYPE html>
<html lang="en">
<head>
<meta charset="utf-8">
<title>Kestrel Building Services – Business Card</title>
<link rel="stylesheet" href="https://fonts.googleapis.com/css2?family=Questrial&family=Lato:wght@400&family=Open+Sans:wght@400&family=Playfair+Display:wght@700&display=swap">
<style>
  :root {
    --backdrop: #6e3a1a;
    --kraft-light: #d9ad80;
    --kraft-mid: #c79564;
    --kraft-dark: #b47f4d;
    --ink: #141008;
    --ink-soft: #3a2a1a;
    --rule: #4a3522;
  }
  * { margin: 0; padding: 0; box-sizing: border-box; }
  html, body {
    width: 1200px; height: 900px; overflow: hidden;
    background: var(--backdrop);
  }
  .canvas { position: relative; width: 1200px; height: 900px; }
  .card {
    position: absolute;
    width: 556px; height: 342px;
    background: linear-gradient(160deg, var(--kraft-light) 0%, var(--kraft-mid) 45%, var(--kraft-dark) 100%);
    color: var(--ink);
    text-align: center;
  }
  .card--front { left: 330px; top: 91px; }
  .card--back { left: 330px; top: 470px; width: 558px; }

  .person-name {
    position: absolute; left: 0; right: 0; top: 58px;
    font-family: "Questrial", sans-serif; font-weight: 700;
    font-size: 25px; letter-spacing: 1px; line-height: 1;
    -webkit-text-stroke: 0.6px var(--ink);
  }
  .person-title {
    position: absolute; left: 0; right: 0; top: 83px;
    font-family: "Lato", sans-serif; font-size: 15px; color: var(--ink-soft);
  }
  .icon-row {
    position: absolute; left: 192px; top: 106px; width: 176px; height: 22px;
    display: flex; align-items: center; justify-content: center; gap: 3px;
  }
  .icon-row::before, .icon-row::after {
    content: ""; flex: 1; height: 1px; background: var(--rule); margin: 0 6px;
  }
  .contact-icon { width: 20px; height: 20px; }
  .contact-lines {
    position: absolute; left: 0; right: 0; top: 137px;
    font-family: "Open Sans", sans-serif; font-size: 15.5px; line-height: 20px;
  }
  .divider {
    position: absolute; left: 196px; width: 164px; top: 226px;
    height: 1px; background: var(--rule);
  }
  .company-address {
    position: absolute; left: 0; right: 0; top: 237px;
    font-family: "Open Sans", sans-serif; font-size: 15.5px; line-height: 20px;
    font-style: normal;
  }

  .brand-mark {
    position: absolute; left: 249px; top: 92px;
    width: 60px; height: 60px; background: var(--ink);
  }
  .brand-name {
    position: absolute; left: 0; right: 0; top: 164px;
    font-family: "Playfair Display", serif; font-weight: 700;
    font-size: 26px; letter-spacing: 0.5px; line-height: 1.2;
  }
  .brand-tagline {
    position: absolute; left: 0; right: 0; top: 205px;
    font-family: "Open Sans", sans-serif; font-size: 15.5px; letter-spacing: 0.3px;
  }
  .footer-rule {
    position: absolute; top: 292px; height: 1px; width: 94px; background: var(--rule);
  }
  .footer-rule--left { left: 126px; }
  .footer-rule--right { left: 338px; }
  .social-row {
    position: absolute; left: 226px; top: 281px; width: 96px; height: 23px;
    display: flex; justify-content: space-between;
  }
  .social-dot {
    width: 23px; height: 23px; border-radius: 50%; background: var(--ink);
  }
</style>
</head>
<body>
<main class="canvas">
  <section class="card card--front" aria-label="Business card front">
    <h1 class="person-name">MARCUS HALE</h1>
    <p class="person-title">Managing Director</p>
    <div class="icon-row">
      <svg class="contact-icon" viewBox="0 0 20 20" aria-label="Phone"><circle cx="10" cy="10" r="10" fill="var(--ink)"/><path d="M5 8.5c0-2 10-2 10 0v1h-2.5v-1h-5v1H5z M6.5 10.5h7l1 4h-9z" fill="var(--kraft-light)"/></svg>
      <svg class="contact-icon" viewBox="0 0 20 20" aria-label="Mobile"><circle cx="10" cy="10" r="10" fill="var(--ink)"/><path d="M5 8.5c0-2 10-2 10 0v1h-2.5v-1h-5v1H5z M6.5 10.5h7l1 4h-9z" fill="var(--kraft-light)"/></svg>
      <svg class="contact-icon" viewBox="0 0 20 20" aria-label="Email"><circle cx="10" cy="10" r="10" fill="var(--ink)"/><rect x="5" y="6.5" width="10" height="7" fill="var(--kraft-light)"/><path d="M5 6.5l5 4 5-4" stroke="var(--ink)" stroke-width="1" fill="none"/></svg>
      <svg class="contact-icon" viewBox="0 0 20 20" aria-label="Website"><circle cx="10" cy="10" r="10" fill="var(--ink)"/><circle cx="10" cy="10" r="5" fill="none" stroke="var(--kraft-light)" stroke-width="1.4"/><path d="M5 10h10M10 5v10" stroke="var(--kraft-light)" stroke-width="1.2"/></svg>
    </div>
    <div class="contact-lines">
      <p>0800 555 014</p>
      <p>021 555 0193</p>
      <p>info@kestrelgroup.example.nz</p>
      <p>www.kestrelgroup.example.nz</p>
    </div>
    <div class="divider"></div>
    <address class="company-address">
      <p>KESTREL BUILDING SERVICES LTD</p>
      <p>48 Tarata Road, Mangere,</p>
      <p>Auckland 2022, Newzealand</p>
    </address>
  </section>

  <section class="card card--back" aria-label="Business card back">
    <div class="brand-mark" role="img" aria-label="Company mark"></div>
    <h2 class="brand-name">KESTREL BUILDING SERVICES</h2>
    <p class="brand-tagline">AMAZING SERVICES AFFORDABLE PRICE</p>
    <div class="footer-rule footer-rule--left"></div>
    <div class="social-row" role="img" aria-label="Social media links">
      <span class="social-dot"></span>
      <span class="social-dot"></span>
      <span class="social-dot"></span>
      <span class="social-dot"></span>
    </div>
    <div class="footer-rule footer-rule--right"></div>
  </section>
</main>
</body>
</html>
```